Small legal and financial translation company needs Squarespace website, brochure and logo

Hello,
We are Lumarin Services (www.lumarinservices-example.com), a boutique legal and financial translation company. We offer our services mainly to Spanish customers. Our primary line of business is the translation of financial statements, but we translate a wide variety legal and financial texts.
The project we are offering comprises three parts: a redo of the current website, an informational brochure for potential customer and a logo design. These three parts should provide a consistent image. We would develop content soon.
We are looking for a website that would look like a typical law firm website, nothing too fancy. Right now, it is in English, Spanish and French, although the new site need only be in English and Spanish. There must be good toggling between the English and Spanish versions. There would be no need for tie-ins to social media and it would not contain a blog. Basically, a static site. We aren't interesting in driving traffic to the site or SEO, as we will contact nearly all potential customers beforehand. The website must be built in Squarespace to enable a smooth transition. The content would be similar to the current page, we'll be working on the exact content, but a rough draft is attached.
The brochure will be some three pages and would introduce the company to potential customers, using similar images as the website and the logo to be designed.
The only specifications for the logo is, as the website and brochure, it convey a sense of security and trust.
Feel free to ask with any questions as this is the first time we have used this platform.
Thank you!
Updates

I've added a more or less final version for the text in the brochure and updated the brief. Added Wednesday, June 10, 2015

Target Market(s)

Spanish law firms, auditors, accountants, banks, investment firms

Industry/Entity Type

Finance

Logo Text

Lumarin Services

Number of Pages Required

5+ page

Font styles to use
Serif

Requirements
Must have
• The website must be built in Squarespace and have a good option to toggle between English and Spanish versions.
• Brochure must be in both English and Spanish, I'm attaching a rough draft of the information that it will probably have. This should give an idea about what to include and the spacing. I will update it to include the final information.
Nice to have
• Would be nice to have some quality finance- and legal-related images
Should not have
• Vibrant colours

```html
<!DOCTYPE html>
<html lang="en">
<head>
<meta charset="utf-8">
<title>Lumarin Services – Brochure Cover &amp; Back Page</title>
<link rel="stylesheet" href="https://fonts.googleapis.com/css2?family=Crimson+Text:wght@400;600&display=swap">
<style>
  :root {
    --backdrop: #e4e4e4;
    --ink-black: #0d0d0d;
    --ink-charcoal: #1c1c1c;
    --paper-white: #ffffff;
    --brand-red: #86101d;
    --brand-red-deep: #55050e;
    --text-light: #e6e6e6;
    --text-muted: #c9c9c9;
    --logo-grey: #2a2a2a;
  }
  * { margin: 0; padding: 0; box-sizing: border-box; }
  html, body {
    width: 1200px; height: 847px; overflow: hidden;
    background: var(--backdrop);
    font-family: "Crimson Text", Georgia, serif;
  }
  .spread {
    position: absolute; left: 100px; top: 70px;
    width: 1000px; height: 707px;
    display: flex;
    box-shadow: 0 10px 30px rgba(0,0,0,.25);
  }
  .page { position: relative; width: 500px; height: 707px; overflow: hidden; }
  .page svg.page-art { position: absolute; inset: 0; width: 500px; height: 707px; }

  /* Back page */
  .back-intro {
    position: absolute; left: 34px; top: 44px; width: 430px;
    color: var(--text-muted); font-size: 13.5px; line-height: 1.5;
  }
  .contact {
    position: absolute; left: 34px; top: 496px; color: var(--text-light);
  }
  .contact-title { font-size: 22px; font-weight: 600; margin-bottom: 8px; color: var(--paper-white); }
  .contact-line { font-size: 13.5px; line-height: 1.7; color: var(--text-muted); }

  /* Cover */
  .brand {
    position: absolute; left: 0; right: 0; top: 22px;
    display: flex; align-items: center; justify-content: center; gap: 10px;
  }
  .brand-square { width: 22px; height: 22px; background: var(--brand-red); }
  .brand-name {
    font-size: 28px; font-weight: 400; color: var(--logo-grey);
    letter-spacing: 2px; text-transform: uppercase;
  }
  .tagline {
    position: absolute; left: 0; right: 0; top: 430px;
    text-align: center; color: var(--paper-white);
    font-size: 25px; font-weight: 400; line-height: 1.3;
  }
  .cover-url {
    position: absolute; left: 0; right: 0; top: 575px;
    text-align: center; color: var(--text-light);
    font-size: 14.5px; letter-spacing: .5px;
  }
</style>
</head>
<body>
<main class="spread">

  <section class="page back-page">
    <svg class="page-art" viewBox="0 0 500 707">
      <defs>
        <linearGradient id="towerTone" x1="0" y1="0" x2="1" y2="1">
          <stop offset="0" stop-color="#151515"/>
          <stop offset=".55" stop-color="#2e2e2e"/>
          <stop offset="1" stop-color="#111"/>
        </linearGradient>
        <linearGradient id="redBand" x1="0" y1="0" x2="1" y2="0">
          <stop offset="0" stop-color="var(--brand-red-deep)"/>
          <stop offset=".6" stop-color="var(--brand-red)"/>
          <stop offset="1" stop-color="#6e0914"/>
        </linearGradient>
      </defs>
      <rect width="500" height="707" fill="var(--ink-black)"/>
      <rect class="tower-photo" width="500" height="455" fill="url(#towerTone)" role="img" aria-label="Low-angle photograph of a glass office tower"/>
      <path class="contact-band" d="M0 455 L500 455 Q430 690 0 707 Z" fill="url(#redBand)"/>
      <path d="M500 455 Q430 690 0 707" fill="none" stroke="#d4d4d4" stroke-width="1.5"/>
      <path d="M0 455 L500 455" stroke="#d4d4d4" stroke-width="1"/>
    </svg>
    <p class="back-intro">Throughout our careers, we have observed a marked deficiency in translations with respect to quality and price. A high-value translation at a reasonable price does seem to be readily available and so we look to offer translations that respect your company's image as much as its pocketbook. In short, a high added-value product of impeccable quality at prices in line with today's dynamics.</p>
    <div class="contact">
      <h2 class="contact-title">Contact Us</h2>
      <p class="contact-line">218 Harbor Crest Avenue, Oakmere, FL 30412</p>
      <p class="contact-line">(555) 014-2290</p>
      <p class="contact-line">info@lumarinservices-example.com</p>
      <p class="contact-line">www.lumarinservices-example.com</p>
    </div>
  </section>

  <section class="page cover-page">
    <svg class="page-art" viewBox="0 0 500 707">
      <defs>
        <linearGradient id="deskTone" x1="0" y1="0" x2="1" y2="0">
          <stop offset="0" stop-color="#d9d9d9"/>
          <stop offset=".5" stop-color="#9a9a9a"/>
          <stop offset="1" stop-color="#5a5a5a"/>
        </linearGradient>
        <linearGradient id="coverBlack" x1="0" y1="0" x2="1" y2="1">
          <stop offset="0" stop-color="var(--ink-black)"/>
          <stop offset=".6" stop-color="var(--ink-charcoal)"/>
          <stop offset="1" stop-color="#050505"/>
        </linearGradient>
      </defs>
      <rect width="500" height="707" fill="var(--paper-white)"/>
      <rect class="desk-photo" y="60" width="500" height="350" fill="url(#deskTone)" role="img" aria-label="Photograph of a lawyer signing documents at a desk beside a statue of Justice"/>
      <path d="M0 0 H500 V64 Q250 76 0 96 Z" fill="var(--paper-white)"/>
      <path d="M0 96 Q250 76 500 64" fill="none" stroke="var(--brand-red)" stroke-width="4"/>
      <path class="accent-triangle" d="M350 300 L500 248 L500 344 Z" fill="var(--brand-red)"/>
      <path class="cover-base" d="M0 405 Q250 350 500 340 L500 707 L0 707 Z" fill="url(#coverBlack)"/>
    </svg>
    <div class="brand">
      <span class="brand-square"></span>
      <span class="brand-name">Lumarin Services</span>
    </div>
    <h1 class="tagline">High-quality translation services<br>in English, Spanish and French<br>for legal and financial documents</h1>
    <p class="cover-url">www.lumarinservices-example.com</p>
  </section>

</main>
</body>
</html>
```